Geschäftspapiere für Fliesenleger - Meisterbetrieb
Zielgruppe
Wir sind ein mittelständischer Fliesenleger - Meisterbetrieb und möchten unsere Geschäftspapiere erneuern. Unsere Kunden sind Privatkunden, Gewerbetreibende sowie Öffentliche Auftraggeber.
Aufgabenstellung
Unser Logo stellen wir Ihnen zur verfügung und soll unverändert bleiben.
Wir benötigen folgende Geschäftspapiere:
- Briefpapier DIN A4
- Notizblock Karriert DIN A4
- Visitenkarten 5,5 x 8,5 cm
- Kuvert DIN lang mit Fenster
- Kuvert DIN C4 mit Fenster
Bei der Farbe Rot handelt es sich um Verkehrsrot RAL 3020
Als Schriftart haben wir uns Helvetica Neue vorgestellt.
Wir bitten jedoch auch um Vorschläge anderer Moderner und gut lesbarer Schriftarten die für Print und Web bestens geeignet sind.
Wir wünschen uns ein Modernes und Schnörkelloses Design. Bei den Dateien habe ich Ihnen ein Stockphoto angehängt um Ihnen zu zeigen wie wir uns ein Cover oder eine Broschüre vorstellen können. Nur um Ihnen unsere Ideen / Vorstellungen näher zu bringen.

```html
<!DOCTYPE html>
<html lang="de">
<head>
<meta charset="utf-8">
<title>Ferrano – Geschäftsausstattung</title>
<link href="https://fonts.googleapis.com/css2?family=Inter:wght@400;500;600&display=swap" rel="stylesheet">
<style>
  :root {
    --red: #e8191a;
    --ink: #222226;
    --grey-text: #555559;
    --paper: #ffffff;
    --backdrop: #ececed;
    --dark: #2a2a2e;
    --photo-tone: linear-gradient(135deg, #8c8c8c 0%, #4a4a4a 60%, #2e2e2e 100%);
    --tile-tone: linear-gradient(135deg, #cfc6b8 0%, #b9b0a2 50%, #9e978c 100%);
  }
  * { box-sizing: border-box; margin: 0; padding: 0; }
  html, body { width: 1200px; height: 1200px; overflow: hidden; }
  body {
    background: var(--backdrop);
    font-family: "Inter", "Helvetica Neue", Arial, sans-serif;
    color: var(--ink);
    position: relative;
  }
  .piece { position: absolute; background: var(--paper); }
  .wordmark { font-weight: 500; color: var(--red); letter-spacing: -0.01em; line-height: 1; }
  .tag { font-size: 5px; color: var(--red); margin-top: 3px; }
  .tiny { font-size: 5.5px; line-height: 7.5px; color: var(--grey-text); }

  /* Compliment card, red */
  .compliment-card { left: 425px; top: 185px; width: 350px; height: 143px; background: var(--red); }
  .compliment-card .wordmark { position: absolute; left: 11px; top: 108px; font-size: 20px; color: #fff; }
  .compliment-card .tag { position: absolute; left: 11px; top: 126px; color: #fff; opacity: .85; }

  /* Letterhead */
  .letterhead { left: 425px; top: 359px; width: 351px; height: 448px; }
  .letterhead .accent-top { position: absolute; right: 23px; top: 21px; width: 54px; height: 3px; background: var(--red); }
  .letter-title { position: absolute; left: 37px; top: 31px; font-size: 11px; font-weight: 600; }
  .letter-date { position: absolute; left: 37px; top: 49px; font-size: 8px; color: var(--grey-text); }
  .letter-body { position: absolute; left: 37px; top: 79px; width: 276px; font-size: 7.6px; line-height: 11px; color: var(--ink); }
  .letter-body p { margin-bottom: 8px; }
  .letter-body .narrow { width: 210px; }
  .letter-sign { font-weight: 600; }
  .letter-photo { position: absolute; left: 167px; top: 330px; width: 164px; height: 118px; background: var(--photo-tone); }
  .letter-footer { position: absolute; left: 0; top: 368px; width: 108px; }
  .letter-footer .rule { position: absolute; left: 0; top: 0; width: 108px; height: 2px; background: var(--red); }
  .letter-footer .rule-right { position: absolute; left: 230px; top: 0; width: 98px; height: 2px; background: var(--red); }
  .letter-footer .url { position: absolute; left: 37px; top: -5px; font-size: 5px; color: var(--red); background: var(--paper); padding: 0 3px; }

  /* Note card */
  .note-card { left: 152px; top: 383px; width: 220px; height: 201px; }
  .note-card .brand { position: absolute; left: 10px; top: 18px; }
  .note-card .wordmark { font-size: 14px; }
  .note-card .tiny { position: absolute; left: 14px; top: 168px; }

  /* C4 envelope */
  .c4-envelope { left: 138px; top: 627px; width: 256px; height: 375px; }
  .c4-envelope .flap { position: absolute; left: 0; top: 0; width: 256px; height: 129px; background: var(--dark); border-radius: 0 0 10px 10px; }
  .c4-envelope .brand { position: absolute; left: 10px; top: 14px; }
  .c4-envelope .wordmark { font-size: 14px; }
  .c4-envelope .flap .tiny { position: absolute; left: 12px; top: 100px; color: #c9c9cc; }
  .c4-envelope .sender { position: absolute; left: 10px; top: 350px; }

  /* Business card */
  .business-card { left: 868px; top: 682px; width: 197px; height: 121px; }
  .business-card .brand { position: absolute; left: 11px; top: 13px; }
  .business-card .wordmark { font-size: 15px; }
  .business-card .contact { position: absolute; left: 12px; top: 91px; }
  .business-card .red-block { position: absolute; right: 0; bottom: 0; width: 57px; height: 51px; background: var(--red); }
  .business-card .red-block .tiny { position: absolute; left: 8px; top: 14px; color: #fff; }

  /* Business card, reverse */
  .card-reverse { left: 464px; top: 857px; width: 186px; height: 122px; }
  .card-reverse .tiles { position: absolute; inset: 0; background: var(--tile-tone); }
  .card-reverse .red-block { position: absolute; right: 0; bottom: 0; width: 58px; height: 52px; background: var(--red); }
  .card-reverse .red-block .tiny { position: absolute; left: 7px; top: 14px; color: #fff; }

  /* DL envelope */
  .dl-envelope { left: 689px; top: 856px; width: 374px; height: 167px; }
  .dl-envelope .brand { position: absolute; left: 15px; top: 16px; }
  .dl-envelope .wordmark { font-size: 15px; }
</style>
</head>
<body>

  <section class="piece compliment-card">
    <div class="wordmark">ferrano</div>
    <div class="tag">Meisterbetrieb</div>
  </section>

  <section class="piece letterhead">
    <div class="accent-top"></div>
    <h1 class="letter-title">Tiling Craftsman</h1>
    <div class="letter-date">März 2024</div>
    <div class="letter-body">
      <p>Sehr geehrte Damen und Herren,</p>
      <p>wir danken Ihnen für Ihre Anfrage und freuen uns, Ihnen unser Angebot für die Verlegung neuer Fliesen in Bad und Küche zu senden. Alle Arbeiten führen wir sauber, termingerecht und in Meisterqualität aus.</p>
      <p>Der Preis enthält Material, Abdichtung und Fugen. Gern beraten wir Sie vor Ort zu Formaten, Farben und Oberflächen.</p>
      <p>Bei Rückfragen erreichen Sie uns jederzeit telefonisch oder per E-Mail. Wir freuen uns auf Ihren Auftrag.</p>
      <p class="narrow">Mit freundlichen Grüßen aus unserem Meisterbetrieb und bis bald auf Ihrer Baustelle.</p>
      <p class="letter-sign">Team Ferrano</p>
    </div>
    <div class="letter-photo" role="img" aria-label="Schwarzweißfoto: zwei Fliesenleger im Gespräch an einem Arbeitstisch"></div>
    <div class="letter-footer">
      <div class="rule"></div>
      <div class="rule-right"></div>
      <span class="url">ferrano.de</span>
    </div>
  </section>

  <section class="piece note-card">
    <div class="brand">
      <div class="wordmark">ferrano</div>
      <div class="tag">Meisterbetrieb</div>
    </div>
    <div class="tiny">Notizen<br>Fliesenweg 12<br>Düsseldorf</div>
  </section>

  <section class="piece c4-envelope">
    <div class="flap">
      <div class="brand">
        <div class="wordmark">ferrano</div>
        <div class="tag">Meisterbetrieb</div>
      </div>
      <div class="tiny">Fliesenweg 12<br>40210 Düsseldorf<br>Tel. 0211 4455</div>
    </div>
    <div class="tiny sender">Ferrano GmbH<br>Düsseldorf</div>
  </section>

  <section class="piece business-card">
    <div class="brand">
      <div class="wordmark">ferrano</div>
      <div class="tag">Meisterbetrieb</div>
    </div>
    <div class="tiny contact">Jonas Hart<br>Fliesenlegermeister<br>0171 2233445</div>
    <div class="red-block"><div class="tiny">Mobil<br>Büro<br>Web</div></div>
  </section>

  <section class="piece card-reverse">
    <div class="tiles" role="img" aria-label="Fotomotiv: Fliesenmuster in Beige und Grau mit Werkzeugen"></div>
    <div class="red-block"><div class="tiny">Fliesen<br>Platten<br>Naturstein</div></div>
  </section>

  <section class="piece dl-envelope">
    <div class="brand">
      <div class="wordmark">ferrano</div>
      <div class="tag">Meisterbetrieb</div>
    </div>
  </section>

</body>
</html>
```